Business cards for a fun web development agency

Hi,I am building a web development agency. You can read about it on the website http://kite-loft.examplehost.com. Basically, I want to focus on free and open source products and stay as far away from the corporate business feeling as possible. I want to build a community so I want the business card to feel fun and approachable (at the risk of professional if need be). I am uploading some of my image assets in various file formats. Feel free to use them or make your own if you want just keeping in theme with the website.
Industry/Entity Type
Building
Contact Information for Business Card
Company Name: Boat ShedWebsite: www.kiteloftdev.example (it's currently in alpha on http://kite-loft.examplehost.com if you want to see the them we are trying to capture)My name is: Banner B. SchaferMy email: banner@boatsheddev.comMy phone: 0431 587 904
Look and feel

```html
<!DOCTYPE html>
<html lang="en">
<head>
<meta charset="utf-8">
<title>Kite Loft business cards</title>
<link rel="stylesheet" href="https://fonts.googleapis.com/css2?family=Arimo:wght@400;500&display=swap">
<style>
  :root {
    --page: #e6e6e6;
    --card: #ffffff;
    --brand-blue: #1a86b6;
    --ink-slate: #3f5a86;
    --mark-faint: #eef1f6;
    --mark-ring: #e4e9f1;
  }
  html, body {
    margin: 0;
    padding: 0;
    width: 1189px;
    height: 1200px;
    overflow: hidden;
    background: var(--page);
    font-family: "Arimo", Arial, sans-serif;
  }
  .sheet {
    position: relative;
    width: 1189px;
    height: 1200px;
  }
  .card {
    position: absolute;
    left: 171px;
    width: 855px;
    height: 487px;
    background: var(--card);
    overflow: hidden;
  }
  .card--front { top: 66px; }
  .card--back { top: 626px; }

  .wordmark {
    position: absolute;
    left: 0;
    right: 0;
    top: 172px;
    height: 144px;
    margin: 0;
    display: flex;
    justify-content: center;
    align-items: flex-end;
    gap: 6px;
    font-size: 104px;
    font-weight: 400;
    line-height: 1;
    color: var(--brand-blue);
    text-transform: uppercase;
  }
  .wordmark__word {
    display: block;
    padding-bottom: 26px;
    letter-spacing: 1px;
  }
  .wordmark__dot {
    display: block;
    width: 144px;
    height: 144px;
    border-radius: 50%;
    background: var(--brand-blue);
    flex: none;
  }

  .back-mark {
    position: absolute;
    left: 0;
    top: 0;
  }

  .contact {
    position: absolute;
    left: 0;
    right: 0;
    top: 140px;
    text-align: center;
  }
  .contact__name {
    margin: 0 0 34px;
    font-size: 52px;
    font-weight: 500;
    line-height: 60px;
    color: var(--brand-blue);
  }
  .contact__lines {
    margin: 0;
    font-size: 35px;
    font-weight: 500;
    line-height: 42px;
    color: var(--ink-slate);
  }
</style>
</head>
<body>
<main class="sheet">
  <section class="card card--front">
    <h1 class="wordmark" aria-label="Kite Loft">
      <span class="wordmark__word">Kite</span>
      <span class="wordmark__dot" aria-hidden="true"></span>
      <span class="wordmark__word">Loft</span>
    </h1>
  </section>

  <section class="card card--back">
    <svg class="back-mark" width="855" height="487" viewBox="0 0 855 487" aria-hidden="true">
      <circle cx="426" cy="239" r="292" fill="var(--mark-faint)" stroke="var(--mark-ring)" stroke-width="14"/>
    </svg>
    <div class="contact">
      <h2 class="contact__name">Corwin T. Aldous</h2>
      <p class="contact__lines">
        0431 587 904<br>
        www.kiteloftdev.example<br>
        corwin@kiteloftdev.example
      </p>
    </div>
  </section>
</main>
</body>
</html>
```